Velmarotix - world unique technology for better life - please let them know who am i at first sight

We need a new business card for company which is a provider of unique crystal based technology suitable for all living being. For more information and final design you can use our brochure (our colours are black and blue from brochure).
We use Verdana font

Industry/Entity Type

Business

Contact Information for Business Card

regular dimension

Font styles to use
Other font styles liked:
• Verdana

Requirements
Must have
• Logo
• name
• function/position
• phone
• mobile
• e-mail
• adress
Nice to have
• inovative design (technology directed)

```html
<!DOCTYPE html>
<html lang="en">
<head>
<meta charset="utf-8">
<title>Velmarotix – Business Card</title>
<link rel="stylesheet" href="https://fonts.googleapis.com/css2?family=Noto+Sans:ital,wght@0,400;0,600;1,400&display=swap">
<style>
  :root {
    --canvas-bg: #e4e6ea;
    --card-white: #ffffff;
    --card-mist: #e9eaec;
    --brand-blue: #0aa3e2;
    --brand-blue-deep: #0893cf;
    --accent-grey: #a7a9ac;
    --ink: #2b2b2b;
    --on-blue: #ffffff;
  }
  * { margin: 0; padding: 0; box-sizing: border-box; }
  html, body {
    width: 1200px; height: 840px; overflow: hidden;
    background: var(--canvas-bg);
    font-family: "Noto Sans", Verdana, sans-serif;
  }
  .card {
    position: absolute; left: 75px; top: 120px;
    width: 1050px; height: 600px;
    background: linear-gradient(160deg, var(--card-white) 0%, var(--card-mist) 100%);
    box-shadow: 0 14px 40px rgba(0,0,0,0.18);
    overflow: hidden;
  }
  .card__waves { position: absolute; inset: 0; width: 100%; height: 100%; }
  .brand {
    position: absolute; left: 440px; top: 40px;
    display: flex; align-items: center; gap: 22px;
  }
  .brand__dot {
    width: 100px; height: 100px; border-radius: 50%;
    background: var(--brand-blue);
  }
  .brand__name {
    font-size: 62px; font-weight: 400; letter-spacing: 2px;
    color: var(--brand-blue); line-height: 1;
  }
  .person {
    position: absolute; right: 110px; top: 162px; text-align: right;
  }
  .person__name {
    font-size: 32px; font-weight: 600; letter-spacing: 1px;
    color: var(--ink); text-transform: uppercase; line-height: 1.15;
  }
  .person__role {
    font-size: 23px; font-style: italic; color: var(--brand-blue); line-height: 1.3;
  }
  .address {
    position: absolute; right: 40px; top: 330px; text-align: right;
    font-size: 21px; line-height: 1.4; color: var(--on-blue);
  }
  .contacts {
    position: absolute; left: 34px; top: 420px;
    list-style: none; color: var(--on-blue); font-size: 21px;
  }
  .contacts__item {
    display: flex; align-items: center; gap: 14px; height: 34px;
  }
  .contacts__icon { width: 21px; height: 21px; flex: none; }
</style>
</head>
<body>
  <main class="card">
    <svg class="card__waves" viewBox="0 0 1050 600" aria-hidden="true">
      <path d="M0,352 C220,298 420,288 580,293 C760,298 900,270 1050,205 L1050,228 C900,292 760,320 580,316 C420,311 220,322 0,375 Z" fill="var(--accent-grey)"/>
      <path d="M0,395 C220,340 420,330 580,335 C760,340 900,315 1050,250 L1050,600 L0,600 Z" fill="var(--brand-blue)"/>
      <path d="M0,600 L0,570 C350,550 700,530 1050,480 L1050,600 Z" fill="var(--brand-blue-deep)" opacity="0.5"/>
    </svg>

    <div class="brand">
      <span class="brand__dot"></span>
      <span class="brand__name">Velmarotix</span>
    </div>

    <div class="person">
      <p class="person__name">Daniel Morrow</p>
      <p class="person__role">Managing Director</p>
    </div>

    <p class="address">27.9th floor.Plaza<br>Harbor Road NRT</p>

    <ul class="contacts">
      <li class="contacts__item">
        <svg class="contacts__icon" viewBox="0 0 24 24"><path d="M6 2l4 4-2 3c1 3 4 6 7 7l3-2 4 4-3 3C11 20 4 13 3 5z" fill="currentColor"/></svg>
        014 582 3067
      </li>
      <li class="contacts__item">
        <svg class="contacts__icon" viewBox="0 0 24 24"><rect x="6" y="1" width="12" height="22" rx="2" fill="none" stroke="currentColor" stroke-width="2"/><circle cx="12" cy="19" r="1.4" fill="currentColor"/></svg>
        014 582 3068
      </li>
      <li class="contacts__item">
        <svg class="contacts__icon" viewBox="0 0 24 24"><rect x="3" y="9" width="18" height="12" fill="currentColor"/><rect x="7" y="3" width="10" height="7" fill="none" stroke="currentColor" stroke-width="2"/></svg>
        014 582 3069
      </li>
      <li class="contacts__item">
        <svg class="contacts__icon" viewBox="0 0 24 24"><rect x="2" y="5" width="20" height="14" fill="none" stroke="currentColor" stroke-width="2"/><path d="M2 5l10 8 10-8" fill="none" stroke="currentColor" stroke-width="2"/></svg>
        contact@velmarotix.com
      </li>
      <li class="contacts__item">
        <svg class="contacts__icon" viewBox="0 0 24 24"><circle cx="12" cy="12" r="10" fill="none" stroke="currentColor" stroke-width="2"/><ellipse cx="12" cy="12" rx="4.5" ry="10" fill="none" stroke="currentColor" stroke-width="1.6"/><path d="M2 12h20M4 7h16M4 17h16" stroke="currentColor" stroke-width="1.4"/></svg>
        www.velmarotix.com
      </li>
    </ul>
  </main>
</body>
</html>
```